Set of 6 Illustrations for Transport Security Platform – Duvrelt

Duvrelt is an innovative solution that enhances safety in transport and logistics, based on identity verification, access control, and collaboration within a network of verified subcontractors.
The purpose of the graphics is to present the system’s key functionalities in a modern, technological way that aligns with the brand’s visual identity.
The website will feature a clean and bright aesthetic:
Background: white or light gray (#f7f7f7)
Text: black or dark gray (#1a1a1a)
Accent color: green (#27ae60 or #2ecc71) – symbolizing safety and trust
The graphics should be stylistically consistent, simple, and easy to read — ideally created in a flat design or isometric 3D style with subtle gradients.
We should avoid stock photos of people or trucks — the goal is a symbolic and technological visual approach.
I initially prepared the graphics myself in Canva, but they are not visually consistent.
Colors
Designer to choose only greyscale colors for use in the design.
Look and feel
Each slider illustrates characteristics of the customer's brand and the style your logo design should communicate.

```html
<!DOCTYPE html>
<html lang="en">
<head>
<meta charset="utf-8">
<title>Duvrelt – verification flow</title>
<link rel="stylesheet" href="https://fonts.googleapis.com/css2?family=Raleway:wght@500;600;700&family=Oswald:wght@500;600&display=swap">
<style>
  :root{
    --green:#23ae5f;
    --green-soft:#7ec683;
    --green-pale:#dfe8e1;
    --stage:#eeeeee;
    --ink:#1a1a1a;
    --white:#ffffff;
  }
  *{box-sizing:border-box;margin:0;padding:0}
  html,body{width:1200px;height:792px;overflow:hidden;background:var(--white)}
  body{font-family:"Raleway",sans-serif;color:var(--ink)}
  .canvas{position:relative;width:1200px;height:792px}
  .stage{position:absolute;left:0;top:87px;width:866px;height:676px;background:var(--stage);border-radius:82px}
  .links{position:absolute;left:0;top:0}
  .card{position:absolute;background:var(--white);border:3px solid var(--green);border-radius:14px}
  .card--round{border-radius:22px}
  .title{font-weight:700;font-size:18px}
  .name{font-weight:600;font-size:15px}
  .btn{position:absolute;display:flex;align-items:center;justify-content:center;gap:8px;background:var(--green);color:var(--white);font-weight:700;border-radius:20px}
  .details{position:absolute;right:8px;bottom:-3px;width:82px;height:30px;background:var(--green);border-radius:15px 15px 0 0;color:var(--white);font-family:"Oswald",sans-serif;font-weight:500;font-size:16px;display:flex;align-items:center;justify-content:center;gap:4px;z-index:2}
  .details .dot{width:14px;height:14px;border-radius:50%;background:var(--white);display:flex;align-items:center;justify-content:center;gap:1px}
  .details .dot i{width:2px;height:2px;background:var(--green);border-radius:50%}
  .stamp{position:relative;display:inline-block;font-family:"Oswald",sans-serif;font-weight:500;color:var(--green);font-size:16px;line-height:30px;padding:0 6px;letter-spacing:.2px}
  .stamp::before,.stamp::after{content:"";position:absolute;top:0;bottom:0;width:7px;border:3px solid currentColor;border-radius:4px}
  .stamp::before{left:0;border-right:none}
  .stamp::after{right:0;border-left:none}
  .stamp--dark{color:var(--ink)}
  .stamp-row{position:absolute;display:flex;align-items:center;gap:5px}
  .figure{position:absolute;background:linear-gradient(180deg,#6cc48e,var(--green));border-radius:26px 26px 4px 4px}
  .start-tab{position:absolute;left:113px;top:166px;width:83px;height:34px;background:var(--green);border-radius:14px 14px 0 0;color:var(--white);font-weight:600;font-size:13px;text-align:center;padding-top:8px}
  .check-panel{position:absolute;left:57px;top:420px;width:194px;height:261px;background:var(--green);border-radius:22px;color:var(--white)}
  .check-head{position:absolute;left:7px;top:9px;width:178px;height:38px;background:var(--white);border-radius:18px;color:var(--ink);font-weight:600;font-size:15px;display:flex;align-items:center;justify-content:center}
  .check-item{position:absolute;left:20px;display:flex;align-items:center;gap:12px;font-weight:600;font-size:15px;line-height:15px}
  .check-item svg{flex:none}
  .detail-line{text-align:center;font-size:14px;font-weight:500;line-height:19px}
  .detail-line b{font-weight:700}
  .pill{position:absolute;left:8px;width:178px;height:40px;border-radius:20px;background:var(--green-pale);font-weight:600;font-size:15px;line-height:15px;display:flex;align-items:center;justify-content:center;text-align:center}
  .tag{position:absolute;left:8px;padding:2px 6px;border-radius:4px;font-weight:700;font-size:15px}
  .approved-panel{position:absolute;left:907px;top:607px;width:293px;height:185px;background:var(--green);border-radius:22px 0 0 22px;color:var(--ink)}
  .approved-panel .stamp{color:var(--white);font-size:22px;line-height:38px;padding:0 9px}
  .spec{position:absolute;left:13px;top:64px;font-size:15px;line-height:18px;font-weight:500}
  .spec b{font-weight:700}
  .spec span{color:var(--white)}
  .id-card{position:absolute;left:183px;top:104px;width:87px;height:59px;background:var(--white);border-radius:4px}
</style>
</head>
<body>
<div class="canvas">
  <div class="stage"></div>

  <svg class="links" width="1200" height="792" viewBox="0 0 1200 792" fill="none" stroke="var(--green-soft)" stroke-width="15" aria-hidden="true">
    <path d="M251 264 H279 Q289 264 289 274 V495 Q289 505 299 505 H335"/>
    <path d="M430 357 V397"/>
    <path d="M430 377 H561 Q571 377 571 367 V294 Q571 284 581 284 H616"/>
    <path d="M430 536 V566"/>
    <path d="M532 510 H564 Q574 510 574 500 V425 Q574 415 584 415 H616"/>
    <path d="M813 392 H856 Q866 392 866 402 V474 Q866 484 876 484 H907"/>
    <path d="M1000 287 V351"/>
    <path d="M1053 543 V607"/>
  </svg>

  <!-- Step 1 -->
  <div class="start-tab">Start</div>
  <div class="card card--round" style="left:56px;top:195px;width:194px;height:160px">
    <div class="title" style="position:absolute;left:16px;top:14px">Step 1</div>
    <svg style="position:absolute;left:65px;top:60px" width="62" height="32" viewBox="0 0 62 32" aria-hidden="true">
      <path d="M0 10 L24 0 L50 10 V6 H62 V32 H0 Z" fill="var(--green)"/>
      <rect x="6" y="13" width="8" height="6" fill="#fff"/><rect x="18" y="13" width="8" height="6" fill="#fff"/><rect x="30" y="13" width="8" height="6" fill="#fff"/>
    </svg>
    <div class="btn" style="left:6px;top:109px;width:178px;height:38px;font-size:14px">COMPANY FINDER
      <svg width="18" height="18" viewBox="0 0 18 18" fill="none" stroke="#fff" stroke-width="2" aria-hidden="true"><circle cx="7" cy="7" r="5.5"/><path d="M11 11 L17 17"/></svg>
    </div>
  </div>

  <!-- Company check -->
  <div class="check-panel">
    <div class="check-head">Company Check</div>
    <div class="check-item" style="top:62px">
      <svg width="34" height="34" viewBox="0 0 34 34" aria-hidden="true"><circle cx="17" cy="17" r="17" fill="#fff"/><path d="M8 17 L15 24 L27 11" stroke="var(--green)" stroke-width="4" fill="none"/></svg>
      <span style="margin-left:4px">Active</span>
    </div>
    <div class="check-item" style="top:104px">
      <svg width="34" height="34" viewBox="0 0 34 34" aria-hidden="true"><circle cx="17" cy="17" r="17" fill="#fff"/><path d="M8 17 L15 24 L27 11" stroke="var(--green)" stroke-width="4" fill="none"/></svg>
      <span>Company<br>verified</span>
    </div>
    <div class="check-item" style="top:148px">
      <svg width="34" height="34" viewBox="0 0 34 34" aria-hidden="true"><circle cx="17" cy="17" r="17" fill="#fff"/><path d="M8 17 L15 24 L27 11" stroke="var(--green)" stroke-width="4" fill="none"/></svg>
      <span>Verified<br>employee</span>
    </div>
    <div class="check-item" style="top:195px">
      <svg width="34" height="34" viewBox="0 0 34 34" fill="#fff" aria-hidden="true"><circle cx="6" cy="8" r="3"/><circle cx="13" cy="3" r="2.5"/><circle cx="21" cy="5" r="2"/><circle cx="25" cy="12" r="1.8"/><circle cx="25" cy="20" r="1.5"/><circle cx="21" cy="27" r="1.2"/><circle cx="14" cy="30" r="1"/><circle cx="7" cy="27" r="1"/><circle cx="3" cy="19" r="1"/></svg>
      <span>Number of<br>verified drivers</span>
    </div>
  </div>

  <!-- Approved driver -->
  <div class="card" style="left:335px;top:218px;width:197px;height:139px">
    <div class="stamp-row" style="left:14px;top:18px">
      <span class="stamp">APPROVED</span>
      <svg width="20" height="17" viewBox="0 0 22 18" aria-hidden="true"><path d="M2 9 L8 15 L20 2" stroke="var(--green)" stroke-width="3.5" fill="none"/></svg>
    </div>
    <div class="name" style="position:absolute;left:13px;top:62px">Piet Laram</div>
    <div class="figure" role="img" aria-label="Flat illustration of a driver in a cap" style="left:130px;top:14px;width:56px;height:86px"></div>
    <div class="details"><span class="dot"><i></i><i></i><i></i></span>DETAILS</div>
  </div>

  <!-- Approved company -->
  <div class="card" style="left:335px;top:397px;width:197px;height:139px">
    <div class="stamp-row" style="left:14px;top:16px">
      <span class="stamp">APPROVED</span>
      <svg width="20" height="17" viewBox="0 0 22 18" aria-hidden="true"><path d="M2 9 L8 15 L20 2" stroke="var(--green)" stroke-width="3.5" fill="none"/></svg>
    </div>
    <svg style="position:absolute;left:132px;top:20px" width="54" height="28" viewBox="0 0 62 32" aria-hidden="true">
      <path d="M0 10 L24 0 L50 10 V6 H62 V32 H0 Z" fill="var(--green)"/>
      <rect x="6" y="13" width="8" height="6" fill="#fff"/><rect x="18" y="13" width="8" height="6" fill="#fff"/><rect x="30" y="13" width="8" height="6" fill="#fff"/>
    </svg>
    <svg style="position:absolute;left:128px;top:60px" width="58" height="28" viewBox="0 0 64 30" aria-hidden="true">
      <rect x="20" y="0" width="44" height="20" fill="var(--green)"/>
      <path d="M2 10 L8 4 H18 V24 H2 Z" fill="var(--green)"/><rect x="6" y="7" width="6" height="5" fill="#fff"/>
      <rect x="2" y="22" width="62" height="3" fill="var(--green)"/>
      <circle cx="11" cy="26" r="4" fill="var(--green)"/><circle cx="47" cy="26" r="4" fill="var(--green)"/>
    </svg>
    <div class="name" style="position:absolute;left:13px;top:62px">Swift Haul</div>
    <div style="position:absolute;left:13px;top:89px;color:var(--green);font-weight:700;font-size:12px">COMPANY DATA</div>
    <div class="details"><span class="dot"><i></i><i></i><i></i></span>DETAILS</div>
  </div>

  <!-- Drivers count -->
  <div class="card" style="left:335px;top:566px;width:197px;height:139px">
    <div class="stamp-row" style="left:14px;top:18px">
      <span class="stamp">APPROVED</span>
      <svg width="20" height="17" viewBox="0 0 22 18" aria-hidden="true"><path d="M2 9 L8 15 L20 2" stroke="var(--green)" stroke-width="3.5" fill="none"/></svg>
    </div>
    <div class="name" style="position:absolute;left:13px;top:62px">Number of drivers:</div>
    <div style="position:absolute;left:38px;top:82px;color:var(--green);font-weight:700;font-size:32px">35</div>
    <div class="details" style="right:12px"><span class="dot"><i></i><i></i><i></i></span>DETAILS</div>
  </div>

  <!-- Rejected driver -->
  <div class="card" style="left:616px;top:177px;width:197px;height:138px">
    <div class="stamp-row" style="left:18px;top:17px">
      <span class="stamp stamp--dark">REJECTED</span>
      <svg width="16" height="16" viewBox="0 0 18 18" aria-hidden="true"><path d="M2 2 L16 16 M16 2 L2 16" stroke="var(--ink)" stroke-width="3.5"/></svg>
    </div>
    <div class="name" style="position:absolute;left:20px;top:62px">Lena Voss</div>
    <div class="figure" role="img" aria-label="Flat illustration of a female driver" style="left:134px;top:18px;width:54px;height:82px"></div>
    <div class="details" style="right:6px"><span class="dot"><i></i><i></i><i></i></span>DETAILS</div>
  </div>

  <!-- Company details -->
  <div class="card" style="left:616px;top:378px;width:197px;height:284px">
    <svg style="position:absolute;left:65px;top:14px" width="62" height="32" viewBox="0 0 62 32" aria-hidden="true">
      <path d="M0 10 L24 0 L50 10 V6 H62 V32 H0 Z" fill="var(--green)"/>
      <rect x="6" y="13" width="8" height="6" fill="#fff"/><rect x="18" y="13" width="8" height="6" fill="#fff"/><rect x="30" y="13" width="8" height="6" fill="#fff"/>
    </svg>
    <div class="name" style="position:absolute;left:0;right:0;top:56px;text-align:center">Swift Haul</div>
    <div class="detail-line" style="position:absolute;left:0;right:0;top:92px"><b>Vat No.</b> 612048375</div>
    <div class="detail-line" style="position:absolute;left:0;right:0;top:120px"><b>Verified phone no.:</b><br>+32 470 118 263</div>
    <div class="detail-line" style="position:absolute;left:0;right:0;top:169px"><b>Verified bank No.:</b><br>BE417260385912</div>
    <div class="btn" style="left:7px;top:230px;width:177px;height:40px;font-size:13px;letter-spacing:-.3px">ADD TO THE NETWORK +</div>
  </div>

  <!-- Conditions -->
  <div class="card card--round" style="left:904px;top:1px;width:196px;height:286px">
    <div style="position:absolute;left:10px;top:18px;font-weight:600;font-size:15px">Conditions</div>
    <div class="tag" style="top:36px;background:var(--green-soft);color:var(--ink)">Location 1</div>
    <svg style="position:absolute;right:12px;top:12px" width="32" height="44" viewBox="0 0 32 44" aria-hidden="true"><path d="M16 0 A16 16 0 0 1 32 16 C32 28 16 44 16 44 C16 44 0 28 0 16 A16 16 0 0 1 16 0 Z" fill="var(--green)"/><circle cx="16" cy="16" r="6" fill="#fff"/></svg>
    <div class="tag" style="top:80px;background:var(--green);color:var(--white)">Plant 1</div>
    <div class="pill" style="top:126px">Active geofencing<br>required</div>
    <div class="pill" style="top:183px">Verified identity<br>required</div>
    <div class="btn" style="left:54px;top:254px;width:83px;height:33px;border-radius:16px 16px 0 0;font-family:'Oswald',sans-serif;font-weight:500;font-size:17px">NEXT
      <svg width="10" height="12" viewBox="0 0 10 12" aria-hidden="true"><path d="M0 0 L10 6 L0 12 Z" fill="#fff"/></svg>
    </div>
  </div>

  <!-- Step 2 -->
  <div class="card card--round" style="left:907px;top:351px;width:194px;height:192px">
    <div class="title" style="position:absolute;left:13px;top:6px">Step 2</div>
    <div style="position:absolute;left:0;right:0;top:34px;text-align:center;font-weight:600;font-size:15px">Gate portal</div>
    <svg style="position:absolute;left:64px;top:56px" width="62" height="32" viewBox="0 0 62 32" aria-hidden="true">
      <path d="M0 10 L24 0 L50 10 V6 H62 V32 H0 Z" fill="var(--green)"/>
      <rect x="6" y="13" width="8" height="6" fill="#fff"/><rect x="18" y="13" width="8" height="6" fill="#fff"/><rect x="30" y="13" width="8" height="6" fill="#fff"/>
    </svg>
    <div style="position:absolute;left:6px;top:94px;width:178px;height:40px;border:2px solid var(--green);border-radius:20px;display:flex;align-items:center;color:var(--green);font-weight:700;font-size:14px">
      <svg style="margin-left:12px" width="18" height="25" viewBox="0 0 18 25" aria-hidden="true"><path d="M9 0 A9 9 0 0 1 18 9 C18 16 9 25 9 25 C9 25 0 16 0 9 A9 9 0 0 1 9 0 Z" fill="var(--green)"/><circle cx="9" cy="9" r="3.5" fill="#fff"/></svg>
      <span style="margin-left:40px">PLANT 1</span>
    </div>
    <div class="btn" style="left:6px;top:144px;width:178px;height:38px;font-size:14px;gap:36px"><span style="margin-left:10px">VERIFIER</span>
      <svg width="11" height="13" viewBox="0 0 11 13" aria-hidden="true"><path d="M0 0 L11 6.5 L0 13 Z" fill="#fff"/></svg>
    </div>
  </div>

  <!-- Approved entry -->
  <div class="approved-panel">
    <div style="position:absolute;left:16px;top:14px"><span class="stamp">APPROVED</span></div>
    <svg style="position:absolute;left:246px;top:18px" width="24" height="33" viewBox="0 0 24 33" aria-hidden="true"><path d="M12 0 A12 12 0 0 1 24 12 C24 21 12 33 12 33 C12 33 0 21 0 12 A12 12 0 0 1 12 0 Z" fill="#fff"/><circle cx="12" cy="12" r="4.5" fill="var(--green)"/></svg>
    <div style="position:absolute;left:245px;top:53px;font-family:'Oswald',sans-serif;color:var(--white);font-size:11px">GPS</div>
    <div class="spec">
      <b>Driver:</b> <span>Emil Laram</span><br>
      <b>Company:</b> <span>Swift Haul</span><br>
      <b>Truck:</b> <span>KRT4PL82</span><br>
      <b>Truck:</b> <span>Norvik</span><br>
      <b>Truck color:</b> <span>White</span>
    </div>
    <div class="id-card">
      <div style="text-align:center;color:var(--green);font-weight:700;font-size:11px;margin-top:3px">ID CARD</div>
      <svg style="position:absolute;left:5px;top:19px" width="76" height="34" viewBox="0 0 76 34" aria-hidden="true">
        <rect x="1" y="1" width="26" height="32" fill="none" stroke="var(--green)" stroke-width="2"/>
        <circle cx="14" cy="13" r="5" fill="var(--green)"/><path d="M5 32 Q14 18 23 32 Z" fill="var(--green)"/>
        <g fill="var(--green)"><rect x="33" y="3" width="18" height="3"/><rect x="55" y="3" width="20" height="3"/><rect x="33" y="11" width="42" height="3"/><rect x="33" y="19" width="30" height="3"/><rect x="33" y="27" width="24" height="3"/></g>
      </svg>
    </div>
  </div>
</div>
</body>
</html>
```